Flyer for the Lumen 2025 Conference

I am looking to produce a flyer for our upcoming conference, Lumen 2025. This is an annual conference that we plan to publicize on social media. The ideal designer will create a flyer that is eye-catching and effectively communicates the key information. Please see attached our logo, speaker photo, and flyer content.

Target Market(s)

All demographics

Industry/Entity Type

Christian

Font styles to use
Sans Serif

Requirements
Should not have
• Cross, church

```html
<!DOCTYPE html>
<html lang="en">
<head>
<meta charset="utf-8">
<title>Lumen 2025 Conference</title>
<link href="https://fonts.googleapis.com/css2?family=Anton&family=Montserrat:wght@200;300;400;600;700;800;900&display=swap" rel="stylesheet">
<style>
  :root {
    --orange: #f7941d;
    --navy: #0d1f6e;
    --blue: #0a72e8;
    --cyan: #1fd6e8;
    --paper: #f3f3f3;
    --ink: #141a2e;
  }
  * { margin: 0; padding: 0; box-sizing: border-box; }
  html, body { width: 927px; height: 1200px; overflow: hidden; background: var(--paper); }
  .flyer {
    position: relative; width: 927px; height: 1200px; overflow: hidden;
    background: linear-gradient(180deg, #f7f7f7 0%, #efefef 100%);
    font-family: "Montserrat", sans-serif; color: var(--ink);
  }
  .abs { position: absolute; }

  .mic-photo {
    left: 640px; top: 0; width: 287px; height: 555px;
    background: radial-gradient(circle at 60% 30%, #b9b9b9 0%, #d6d6d6 40%, rgba(240,240,240,0) 75%);
  }
  .speaker-photo {
    left: 0; top: 380px; width: 540px; height: 820px;
    background: radial-gradient(ellipse at 45% 55%, #1f6fe0 0%, #1757c4 35%, rgba(23,87,196,0.35) 62%, rgba(240,240,240,0) 78%);
  }

  .topic { left: 67px; top: 54px; }
  .topic-label { color: var(--orange); font-size: 25px; font-weight: 400; line-height: 1.2; }
  .topic-title { font-size: 30px; font-weight: 300; line-height: 1.12; color: var(--ink); }
  .topic-title b { font-weight: 400; }
  .topic-rule { left: 69px; top: 160px; width: 1px; height: 385px; background: var(--navy); }

  .brand { left: 0; width: 927px; top: 62px; text-align: center; }
  .brand-name { display: inline-flex; align-items: center; gap: 8px; font-size: 36px; font-weight: 600; color: var(--navy); letter-spacing: 1px; }
  .brand-dot { width: 14px; height: 14px; border-radius: 50%; background: var(--orange); }

  .event-name {
    left: 278px; top: 118px; width: 375px;
    font-family: "Anton", sans-serif; color: var(--orange);
    font-size: 160px; line-height: 1; text-align: center; letter-spacing: 2px;
  }
  .event-year {
    left: 278px; top: 262px; width: 375px;
    font-family: "Anton", sans-serif; color: var(--navy);
    font-size: 200px; line-height: 1; text-align: center; letter-spacing: 4px;
  }
  .tagline-strong { left: 283px; top: 470px; font-size: 55px; font-weight: 900; color: var(--blue); letter-spacing: 0.5px; }
  .tagline-light { left: 287px; top: 530px; font-size: 54px; font-weight: 200; color: var(--navy); letter-spacing: 1px; }

  .month {
    left: 462px; top: 903px; transform-origin: left top; transform: rotate(-90deg);
    font-size: 36px; font-weight: 800; color: var(--blue); line-height: 1; white-space: nowrap;
  }
  .sessions { left: 507px; top: 710px; width: 352px; }
  .session { position: relative; height: 54px; margin-bottom: 8px; border-radius: 16px; background: var(--navy); }
  .session-date { position: absolute; left: 20px; top: 4px; font-size: 42px; font-weight: 900; color: var(--orange); line-height: 1.1; letter-spacing: -1px; }
  .session-date sup { font-size: 22px; vertical-align: 18px; letter-spacing: 0; }
  .session-time {
    position: absolute; left: 132px; top: 0; right: 0; height: 54px;
    border-radius: 16px; background: var(--blue); color: #fff; padding: 6px 0 0 28px; line-height: 1.15;
  }
  .session-time .day { font-size: 18px; font-weight: 400; }
  .session-time .hours { font-size: 18px; font-weight: 800; white-space: nowrap; }

  .divider { left: 525px; width: 333px; height: 1px; background: var(--ink); }
  .venue-name { left: 525px; top: 936px; font-size: 16.5px; font-weight: 700; color: var(--orange); white-space: nowrap; }
  .venue-pin {
    left: 525px; top: 968px; width: 42px; height: 40px; border-radius: 12px;
    background: linear-gradient(135deg, var(--blue), var(--cyan)); display: flex; align-items: center; justify-content: center;
  }
  .venue-address { left: 578px; top: 972px; font-size: 17px; font-weight: 400; letter-spacing: 1.2px; line-height: 1.1; color: var(--ink); white-space: nowrap; }

  .app-note { left: 527px; top: 1045px; font-size: 20px; font-weight: 400; line-height: 1.08; color: var(--ink); white-space: nowrap; }
  .app-note .hl-orange { color: var(--orange); font-weight: 700; }
  .app-note .hl-blue { color: var(--blue); font-weight: 700; }
  .store-badge { left: 770px; width: 86px; height: 28px; border-radius: 4px; background: #0b0b0b; }

  .speaker-card {
    left: 0; top: 1010px; width: 312px; height: 114px;
    background: var(--navy); border-radius: 0 26px 26px 0; padding: 10px 0 0 68px;
  }
  .speaker-label { font-size: 28px; font-weight: 300; color: var(--orange); line-height: 1.05; }
  .speaker-name { font-size: 29px; font-weight: 800; color: #fff; line-height: 1.1; white-space: nowrap; }

  .contact-bar {
    left: 0; top: 1133px; width: 927px; height: 32px;
    background: linear-gradient(90deg, #1aa8f5 0%, var(--cyan) 100%);
    display: flex; align-items: center; font-size: 20px; color: var(--navy); letter-spacing: 1.3px;
  }
  .contact-item { position: absolute; display: flex; align-items: center; gap: 8px; white-space: nowrap; }
</style>
</head>
<body>
<main class="flyer">
  <div class="abs mic-photo" role="img" aria-label="Soft grey photograph of a stage microphone with bokeh lights"></div>
  <div class="abs speaker-photo" role="img" aria-label="Photograph of the speaker seated, wearing a blue suit"></div>

  <div class="abs topic">
    <p class="topic-label">Topic:</p>
    <p class="topic-title">The <b>Voice</b><br>Of The <b>Lord</b></p>
  </div>
  <div class="abs topic-rule"></div>

  <div class="abs brand">
    <span class="brand-name"><span class="brand-dot"></span>KAROS</span>
  </div>

  <h1 class="abs event-name">LUMEN</h1>
  <p class="abs event-year">2025</p>
  <p class="abs tagline-strong">A PROPHETIC</p>
  <p class="abs tagline-light">CONFERENCE</p>

  <p class="abs month">December</p>
  <div class="abs sessions">
    <div class="session">
      <span class="session-date">26<sup>th</sup></span>
      <div class="session-time"><div class="day">Friday</div><div class="hours">6:30PM - 9:00PM</div></div>
    </div>
    <div class="session">
      <span class="session-date">27<sup>th</sup></span>
      <div class="session-time"><div class="day">Saturday</div><div class="hours">5:30PM - 8:00PM</div></div>
    </div>
    <div class="session">
      <span class="session-date">28<sup>th</sup></span>
      <div class="session-time"><div class="day">Sunday</div><div class="hours">4:30PM - 7:00PM</div></div>
    </div>
  </div>

  <div class="abs divider" style="top:915px"></div>
  <p class="abs venue-name">The Riverside Performing Arts Center</p>
  <div class="abs venue-pin">
    <svg width="20" height="24" viewBox="0 0 20 24"><path d="M10 1C5 1 1.5 4.6 1.5 9.2 1.5 15 10 23 10 23s8.5-8 8.5-13.8C18.5 4.6 15 1 10 1z" fill="#0b1020"/><circle cx="10" cy="9" r="3.4" fill="#1fb8ec"/></svg>
  </div>
  <p class="abs venue-address">318 Millbrook Avenue<br>Ashford, Maine 04017</p>
  <div class="abs divider" style="top:1032px"></div>

  <p class="abs app-note"><span class="hl-orange">Download</span> the<br><span class="hl-blue">KAROS App</span> to stay<br>updated on the event</p>
  <div class="abs store-badge" style="top:1046px"></div>
  <div class="abs store-badge" style="top:1081px"></div>

  <div class="abs speaker-card">
    <p class="speaker-label">SPEAKER:</p>
    <p class="speaker-name">PROPHET<br>JOEL NDAWA</p>
  </div>

  <footer class="abs contact-bar">
    <span class="contact-item" style="left:68px">
      <svg width="20" height="20" viewBox="0 0 20 20" fill="none" stroke="#0d1f6e" stroke-width="2"><circle cx="10" cy="10" r="8.5"/><ellipse cx="10" cy="10" rx="3.6" ry="8.5"/><path d="M1.5 10h17M3 5.5h14M3 14.5h14"/></svg>
      www.karos.org
    </span>
    <span class="contact-item" style="left:358px">
      <svg width="18" height="18" viewBox="0 0 24 24"><path fill="#0d1f6e" d="M6.6 10.8a15.2 15.2 0 0 0 6.6 6.6l2.2-2.2c.3-.3.7-.4 1-.2 1.1.4 2.3.6 3.6.6.6 0 1 .4 1 1V20c0 .6-.4 1-1 1A17 17 0 0 1 3 4c0-.6.4-1 1-1h3.5c.6 0 1 .4 1 1 0 1.3.2 2.5.6 3.6.1.3 0 .7-.2 1z"/></svg>
      207 555 0142
    </span>
    <span class="contact-item" style="left:620px">
      <svg width="20" height="16" viewBox="0 0 20 16"><rect x="0" y="0" width="20" height="16" rx="2" fill="#0d1f6e"/><path d="M2 3l8 6 8-6" fill="none" stroke="#1fc4ee" stroke-width="2"/></svg>
      hello@karos.org
    </span>
  </footer>
</main>
</body>
</html>
```